Quality Monitoring Company Needs a New Site

We are an established company that has a fair number of clients but the site lacks current design standards that we'd like to keep up with. We'd like to mimic the same style of the site on plinkora.com, vetrumo.com, https://brindlecoffer.com/, etc. We'd also like to make sure the designer understands SEO Silos and how it effects the design elements. Attached is the structure that I'd like to follow for the pages. You don't need to design every single sub-page because they'll probably be fairly similar; however, I want to see at least 1 each. Please use the content on our current site for filler areas. Please try to do a good job of understanding what we do so you can use your best judgement on what is needed to be successful. Use our color scheme and the logo should be the side view but I included the AI just in case.
Updates

I am narrowing down on the field of designs that I have received. There are a lot of similarities between the designs I like and don't like. I'd also like to ensure that some of the inner pages get done in the next 5 days so I can see the creativity that is there as well. That is probably what is next -- getting a few inner pages completed so I can see what you can come up with (not based on our current website) because the current "front pages" are all so good and so close.

Industry/Entity Type

Telecommunications

Colors

Designer to choose colors to be used in the design.

Requirements
Must have
• SEO Silo Look and Feel
• Current Colors
Should not have
• No stockphotos whatsoever. NONE.

```html
<!DOCTYPE html>
<html lang="en">
<head>
<meta charset="utf-8">
<title>Voxlane – Quality Assurance</title>
<link href="https://fonts.googleapis.com/css2?family=Poppins:wght@400;500;600;700&display=swap" rel="stylesheet">
<style>
:root{
  --bg:#f5f6fa;
  --blob:#eceef7;
  --navy:#012e5b;
  --navy-text:#0b2a4f;
  --cyan:#07b4e6;
  --body:#555b66;
  --white:#ffffff;
  --footer-line:#1d4a75;
}
*{margin:0;padding:0;box-sizing:border-box}
html,body{width:1200px;height:1180px;overflow:hidden}
body{font-family:'Poppins',sans-serif;background:var(--bg);position:relative;color:var(--body)}
.abs{position:absolute}
.hero-blob{left:0;top:0}
.brand{left:139px;top:64px;display:flex;align-items:center;gap:8px}
.brand-dot{width:22px;height:22px;border-radius:50%;background:var(--cyan)}
.brand-name{font-size:22px;font-weight:600;color:var(--navy-text);letter-spacing:-.3px}
.main-nav{left:404px;top:78px;font-size:12px;color:#2a2f38}
.main-nav a{position:absolute;white-space:nowrap;color:inherit;text-decoration:none}
.main-nav a.active{color:var(--cyan);font-weight:600}
.phone-badge{left:904px;top:64px;width:38px;height:38px;border-radius:50%;background:var(--cyan);display:flex;align-items:center;justify-content:center}
.phone-number{left:950px;top:72px;font-size:14px;font-weight:700;color:var(--navy-text);letter-spacing:.3px}
.dropdown{left:443px;top:102px;width:184px;height:133px;background:var(--white);border-radius:3px;box-shadow:0 6px 18px rgba(20,40,80,.08);z-index:5}
.dropdown a{position:absolute;left:17px;font-size:11px;color:#555;text-decoration:none;white-space:nowrap}
.dropdown .current{left:7px;top:7px;width:170px;height:29px;background:var(--cyan);color:var(--white);font-weight:600;padding:7px 10px;border-radius:2px;font-size:11px}
.page-title{left:139px;top:190px;font-size:31px;font-weight:700;color:var(--navy-text);white-space:nowrap}
.page-title span{color:var(--cyan);font-weight:500}
.title-rule{left:140px;top:239px;width:35px;height:2px;background:var(--cyan)}
.intro{left:143px;width:456px;font-size:11.6px;line-height:19px;color:var(--body)}
.intro.one{top:260px}
.intro.two{top:355px}
.checklist{left:143px;top:432px;list-style:none;font-size:11.6px;color:var(--body)}
.checklist li{height:32.4px;display:flex;gap:12px}
.checklist svg{margin-top:4px;flex:none}
.hero-art{left:640px;top:159px;width:451px;height:427px;border-radius:8px;background:linear-gradient(135deg,#f4cf57 0%,#cfe4f6 35%,#5aa8e8 65%,#2b3a6a 100%);opacity:.85}
.footer-band{left:0;top:806px;width:1200px;height:374px;background:var(--navy)}
.cta{left:211px;top:701px;width:776px;height:211px;border-radius:106px;background:var(--cyan);text-align:center}
.cta h2{margin-top:48px;font-size:44px;font-weight:400;color:var(--white);letter-spacing:.5px}
.cta a{position:absolute;left:310px;top:126px;width:155px;height:36px;border-radius:18px;background:var(--navy);color:var(--white);font-size:13.5px;line-height:36px;text-decoration:none}
.footer-heading{top:966px;font-size:18px;font-weight:700;color:var(--cyan)}
.footer-links a{position:absolute;font-size:11.5px;color:var(--white);text-decoration:none;white-space:nowrap}
.contact-line{font-size:12.6px;color:var(--white);white-space:nowrap}
.footer-brand{left:940px;top:1002px;display:flex;align-items:center;gap:10px}
.footer-brand .brand-dot{width:30px;height:30px}
.footer-brand .brand-name{font-size:28px;color:var(--white)}
.footer-rule{left:140px;top:1133px;width:917px;height:1px;background:var(--footer-line)}
.copyright{left:0;width:1200px;top:1148px;text-align:center;font-size:12.6px;color:var(--white)}
</style>
</head>
<body>

<svg class="abs hero-blob" width="1200" height="620" viewBox="0 0 1200 620" aria-hidden="true">
  <path d="M862 0 C790 120 650 230 690 360 C730 520 900 610 1200 596 L1200 0 Z" fill="var(--blob)"/>
</svg>

<main>
  <h1 class="abs page-title">Quality <span>Assurance</span></h1>
  <div class="abs title-rule"></div>
  <p class="abs intro one">Lorem ipsum dolor sit amet, consectetuer adipiscing elit, sed diam nonummy nibh euismod tincidunt ut laoreet dolore magna aliquam erat volutpat. Ut wisi enim ad minim veniam, quis nostrud exerci tation ullamcorper suscipit lobortis nisl ut aliquip ex ea commodo consequat.</p>
  <p class="abs intro two">Lorem ipsum dolor sit amet, consectetuer adipiscing elit, sed diam nonummy nibh euismod tincidunt ut laoreet dolore magna aliquam erat volutpat. Ut wisi enim ad minim veniam, quis nostrud exerci tation</p>
  <ul class="abs checklist">
    <li><svg width="10" height="8" viewBox="0 0 10 8"><path d="M1 4l3 3 5-6" stroke="var(--cyan)" stroke-width="2" fill="none"/></svg>Consectetuer adipiscing elit sed diam nonummy</li>
    <li><svg width="10" height="8" viewBox="0 0 10 8"><path d="M1 4l3 3 5-6" stroke="var(--cyan)" stroke-width="2" fill="none"/></svg>Nibh euismod tincidunt ut laoreet dolore magna</li>
    <li><svg width="10" height="8" viewBox="0 0 10 8"><path d="M1 4l3 3 5-6" stroke="var(--cyan)" stroke-width="2" fill="none"/></svg>Aliquam erat volutpat. Ut wisi enim ad minim veniam</li>
    <li><svg width="10" height="8" viewBox="0 0 10 8"><path d="M1 4l3 3 5-6" stroke="var(--cyan)" stroke-width="2" fill="none"/></svg>Quis nostrud exerci tation ullamcorper suscipit lobortis</li>
  </ul>
  <div class="abs hero-art" role="img" aria-label="Illustration of a team reviewing a large quality checklist dashboard with charts, surrounded by floating check-mark badges and a potted plant"></div>
</main>

<header>
  <div class="abs brand"><span class="brand-dot"></span><span class="brand-name">Voxlane</span></div>
  <nav class="abs main-nav">
    <a style="left:0">Home</a>
    <a class="active" style="left:59px">Services</a>
    <a style="left:133px">Industries</a>
    <a style="left:216px">Pricing</a>
    <a style="left:279px">Team</a>
    <a style="left:338px">Blog</a>
    <a style="left:389px">Contact Us</a>
  </nav>
  <div class="abs phone-badge">
    <svg width="15" height="15" viewBox="0 0 24 24"><path fill="#fff" d="M6.6 10.8a15.1 15.1 0 006.6 6.6l2.2-2.2c.3-.3.7-.4 1-.2 1.1.4 2.3.6 3.6.6.6 0 1 .4 1 1V20c0 .6-.4 1-1 1C10.6 21 3 13.4 3 4c0-.6.4-1 1-1h3.5c.6 0 1 .4 1 1 0 1.3.2 2.5.6 3.6.1.3 0 .7-.2 1z"/></svg>
  </div>
  <div class="abs phone-number">555-014-2287</div>
  <div class="abs dropdown">
    <a class="current">Quality Assurance</a>
    <a style="top:53px">Coaching</a>
    <a style="top:82px">Sales Performance</a>
    <a style="top:111px">Ai Enabled Voice Analytics</a>
  </div>
</header>

<footer>
  <div class="abs footer-band"></div>
  <section class="abs cta">
    <h2>Give Us A Shout</h2>
    <a>GET IN TOUCH</a>
  </section>

  <h3 class="abs footer-heading" style="left:139px">Quick Links</h3>
  <nav class="footer-links">
    <a style="left:139px;top:1004px">Home</a>
    <a style="left:139px;top:1024px">Services</a>
    <a style="left:139px;top:1044px">System Details</a>
    <a style="left:139px;top:1064px">Pricing</a>
    <a style="left:294px;top:1004px">Team</a>
    <a style="left:294px;top:1024px">Blog</a>
    <a style="left:294px;top:1044px">Contact Us</a>
    <a style="left:294px;top:1064px">Login</a>
  </nav>

  <h3 class="abs footer-heading" style="left:460px">Contact Us</h3>
  <svg class="abs" style="left:462px;top:1009px" width="11" height="15" viewBox="0 0 12 16"><path fill="#fff" d="M6 0a6 6 0 00-6 6c0 4.5 6 10 6 10s6-5.5 6-10a6 6 0 00-6-6zm0 8.5A2.5 2.5 0 116 3.5a2.5 2.5 0 010 5z"/></svg>
  <div class="abs contact-line" style="left:480px;top:1004px">4410 Harlow Ave.</div>
  <div class="abs contact-line" style="left:480px;top:1027px">Brenford, CA 90210</div>
  <svg class="abs" style="left:660px;top:1008px" width="14" height="14" viewBox="0 0 24 24"><path fill="#fff" d="M6.6 10.8a15.1 15.1 0 006.6 6.6l2.2-2.2c.3-.3.7-.4 1-.2 1.1.4 2.3.6 3.6.6.6 0 1 .4 1 1V20c0 .6-.4 1-1 1C10.6 21 3 13.4 3 4c0-.6.4-1 1-1h3.5c.6 0 1 .4 1 1 0 1.3.2 2.5.6 3.6.1.3 0 .7-.2 1z"/></svg>
  <div class="abs contact-line" style="left:682px;top:1004px">555-014-2287</div>
  <svg class="abs" style="left:660px;top:1045px" width="14" height="11" viewBox="0 0 14 11"><path fill="#fff" d="M0 0h14v11H0z"/><path d="M0 0l7 6 7-6" stroke="var(--navy)" stroke-width="1.4" fill="none"/></svg>
  <div class="abs contact-line" style="left:682px;top:1040px">hello@voxlane.com</div>

  <div class="abs footer-brand"><span class="brand-dot"></span><span class="brand-name">Voxlane</span></div>

  <div class="abs footer-rule"></div>
  <p class="abs copyright">Copyright © 2019 VOXLANE.. All Rights Reserved.</p>
</footer>

</body>
</html>
```